Re-style home page - eye-catching and unique design for social commerce website

We need a new concept design for BrinoKet's home page.
We don't want to make huge changes but creating a more professional and eye-catching style.

We need to look very serious like a professional services company and in the same time to look like a social network for e-commerce.

Our logo is very captive and you can use to creating something of harmonious.

This is a re-style and I'm excepted to see unique and fresh design like Glimmora.

Target Market(s)

e-commerce and social

Industry/Entity Type

Social

Number of Pages Required

1 page

Font styles to use
Serif
Sans Serif

Requirements
Must have
• An eye-catching result.
• Search bar with logo and Login How it works and business
• The slogan with login and signup.
• Footer links.
Nice to have
• I would like to open the home page and see only two clear ways:
• -Consumer
• --Search
• --The slogan
• --Login and Signup
• --How it works
• -Business
• --Go to Business area
• Background: City, Shopping.
Should not have
• Scrollbar style!

```html
<!DOCTYPE html>
<html lang="en">
<head>
<meta charset="utf-8">
<title>BrinoKet – Shop directly from your profile</title>
<link href="https://fonts.googleapis.com/css2?family=Open+Sans:wght@400;600;700;800&display=swap" rel="stylesheet">
<style>
  :root {
    --bar: #2b2b2b;
    --white: #ffffff;
    --ink: #1e1e1e;
    --muted: #9a9a9a;
    --search-bg: #e9e9e9;
    --yellow: #f2d629;
    --yellow-dark: #d9bb12;
    --panel: rgba(22, 22, 28, 0.78);
    --chip: #ffffff;
    --social: #4a67a7;
    --link-blue: #1f9ee6;
    --dropdown: #ececec;
  }
  * { box-sizing: border-box; margin: 0; padding: 0; }
  html, body { width: 1200px; height: 909px; overflow: hidden; }
  body { font-family: "Open Sans", Arial, sans-serif; background: var(--bar); position: relative; }

  .site-header { position: absolute; left: 0; top: 0; width: 1200px; height: 91px; background: var(--bar); }
  .brand { position: absolute; left: 127px; top: 16px; display: flex; align-items: center; gap: 10px; }
  .brand-name { color: var(--white); font-weight: 800; font-size: 46px; letter-spacing: -1px; line-height: 1; }
  .brand-dot { width: 26px; height: 26px; border-radius: 50%; background: var(--yellow); }

  .search { position: absolute; left: 436px; top: 30px; width: 333px; height: 35px; display: flex; }
  .search-input { flex: 1; background: var(--search-bg); border-radius: 3px 0 0 3px; color: var(--muted); font-size: 13px; padding: 9px 14px; }
  .search-btn { width: 41px; background: var(--yellow); border-radius: 0 3px 3px 0; display: flex; align-items: center; justify-content: center; }

  .main-nav { position: absolute; left: 786px; top: 37px; color: var(--white); font-size: 13.5px; display: flex; gap: 12px; }
  .login-toggle { position: absolute; left: 979px; top: 30px; width: 92px; height: 35px; border: 2px solid var(--white); border-radius: 3px; color: var(--white); font-weight: 600; font-size: 16px; display: flex; align-items: center; justify-content: center; }

  .hero { position: absolute; left: 0; top: 91px; width: 1200px; height: 764px;
    background:
      radial-gradient(ellipse at 50% 30%, rgba(255,255,255,0.85) 0%, rgba(255,255,255,0) 35%),
      linear-gradient(180deg, #cfc4b4 0%, #b8aa95 45%, #8e7c6e 70%, #c9bca8 100%); }

  .login-dropdown { position: absolute; left: 807px; top: 83px; width: 264px; height: 173px; background: var(--dropdown); border-radius: 3px; padding: 13px 13px; box-shadow: 0 2px 6px rgba(0,0,0,0.25); z-index: 3; }
  .login-dropdown::before { content: ""; position: absolute; right: 36px; top: -8px; border: 8px solid transparent; border-top: 0; border-bottom-color: var(--dropdown); }
  .field { height: 34px; background: var(--white); border: 1px solid #d8d8d8; border-radius: 3px; color: var(--muted); font-size: 12.5px; padding: 8px 11px; margin-bottom: 11px; }
  .login-now { height: 34px; background: var(--yellow); border-bottom: 3px solid var(--yellow-dark); border-radius: 3px; color: var(--ink); font-weight: 600; font-size: 16px; text-align: center; line-height: 32px; }
  .login-help { margin-top: 8px; font-size: 13.5px; color: #333; }
  .login-help .or { color: #2b46c4; }

  .hero-mark { position: absolute; left: 588px; top: 198px; width: 24px; height: 24px; border-radius: 50%; background: var(--yellow); }
  .headline { position: absolute; left: 0; top: 262px; width: 1200px; text-align: center; font-weight: 700; font-size: 26px; color: var(--ink); letter-spacing: -0.5px; }

  .feed-panel { position: absolute; left: 249px; top: 303px; width: 696px; height: 419px; background: var(--panel); border-radius: 3px; box-shadow: 0 3px 10px rgba(0,0,0,0.4); padding: 0 28px; }
  .feed-title { text-align: center; color: var(--white); font-weight: 700; font-size: 25px; margin-top: 19px; letter-spacing: -0.3px; }
  .feed-grid { margin-top: 14px; display: flex; flex-direction: column; gap: 9px; }
  .feed-row { display: flex; justify-content: space-between; }
  .category { height: 41px; background: var(--chip); border-radius: 2px; display: flex; align-items: center; gap: 8px; padding: 0 14px 0 10px; font-size: 12.5px; color: var(--ink); white-space: nowrap; }
  .category svg { width: 22px; height: 22px; flex: none; }
  .tagline { text-align: center; color: var(--white); font-weight: 700; font-size: 26px; margin-top: 17px; letter-spacing: -0.3px; }
  .signin-row { margin-top: 12px; display: flex; align-items: center; justify-content: center; gap: 10px; padding-right: 40px; }
  .social-connect { display: flex; height: 29px; background: var(--social); border-radius: 2px; color: var(--white); font-size: 12px; font-weight: 600; align-items: center; }
  .social-connect .square { width: 30px; height: 29px; border-right: 1px solid rgba(255,255,255,0.3); display: flex; align-items: center; justify-content: center; }
  .social-connect .square span { width: 10px; height: 10px; background: var(--white); }
  .social-connect .label { padding: 0 14px; }
  .default-signin { color: var(--muted); font-size: 12px; }
  .default-signin b { color: var(--link-blue); }

  .site-footer { position: absolute; left: 0; top: 855px; width: 1200px; height: 54px; background: var(--bar); display: flex; justify-content: center; align-items: center; color: var(--white); font-size: 13.5px; gap: 8px; }
</style>
</head>
<body>
  <header class="site-header">
    <div class="brand"><span class="brand-name">BrinoKet</span><span class="brand-dot"></span></div>
    <div class="search">
      <div class="search-input">Search</div>
      <div class="search-btn"><svg width="18" height="18" viewBox="0 0 18 18"><circle cx="7" cy="7" r="5" fill="none" stroke="#222" stroke-width="2"/><line x1="11" y1="11" x2="16" y2="16" stroke="#222" stroke-width="2.5"/></svg></div>
    </div>
    <nav class="main-nav"><span>HOW IT WORKS</span><span>|</span><span>BUSINESS</span></nav>
    <div class="login-toggle">LOGIN</div>
  </header>

  <main class="hero" role="img" aria-label="Blurred busy city shopping street with people crossing">
  </main>

  <div class="login-dropdown">
    <div class="field">Username</div>
    <div class="field">Password</div>
    <div class="login-now">LOGIN NOW</div>
    <p class="login-help">Forgot Your Password <span class="or">or</span> Signup</p>
  </div>

  <span class="hero-mark"></span>
  <h1 class="headline">SHOP DIRECTLY FROM YOUR PROFILE</h1>

  <section class="feed-panel">
    <h2 class="feed-title">SETUP YOUR FEED</h2>
    <div class="feed-grid">
      <div class="feed-row">
        <div class="category"><svg viewBox="0 0 22 22"><circle cx="11" cy="11" r="9" fill="none" stroke="#111" stroke-width="2"/><circle cx="8" cy="9" r="1.3"/><circle cx="14" cy="9" r="1.3"/><path d="M7 13q4 4 8 0" fill="none" stroke="#111" stroke-width="1.6"/></svg>ACTIVE LIFE</div>
        <div class="category"><svg viewBox="0 0 22 22"><path d="M2 6h9v6a4.5 4.5 0 0 1-9 0z"/><path d="M11 9h9v6a4.5 4.5 0 0 1-9 0z"/></svg>ARTS &amp; ENTERTAINMENT</div>
        <div class="category"><svg viewBox="0 0 22 22"><circle cx="11" cy="11" r="9" fill="none" stroke="#111" stroke-width="2"/><circle cx="11" cy="11" r="3"/></svg>AUTOMOTIVE</div>
        <div class="category"><svg viewBox="0 0 22 22"><path d="M1 17h20l-3-5H4z"/><circle cx="11" cy="8" r="3"/></svg>BEAUTY &amp; SPAS</div>
      </div>
      <div class="feed-row">
        <div class="category"><svg viewBox="0 0 22 22"><rect x="4" y="2" width="14" height="18" fill="none" stroke="#111" stroke-width="2"/><line x1="7" y1="2" x2="7" y2="20" stroke="#111" stroke-width="2"/></svg>EDUCATION</div>
        <div class="category"><svg viewBox="0 0 22 22"><rect x="3" y="5" width="16" height="15" rx="2"/><rect x="6" y="2" width="2" height="5"/><rect x="14" y="2" width="2" height="5"/></svg>EVENT PLANNING &amp; SERVICES</div>
        <div class="category"><svg viewBox="0 0 22 22"><circle cx="11" cy="13" r="8"/><rect x="8" y="2" width="6" height="4"/></svg>FINANCIAL SERVICES</div>
        <div class="category"><svg viewBox="0 0 22 22"><rect x="2" y="4" width="8" height="17"/><rect x="12" y="9" width="8" height="12"/></svg>HOTELS</div>
      </div>
      <div class="feed-row">
        <div class="category"><svg viewBox="0 0 22 22"><rect x="8" y="2" width="6" height="18"/><rect x="2" y="8" width="18" height="6"/></svg>HEALTH &amp; MEDICAL</div>
        <div class="category"><svg viewBox="0 0 22 22"><path d="M11 3l9 8h-3v8h-4v-5h-4v5H5v-8H2z"/></svg>HOME SERVICES</div>
        <div class="category"><svg viewBox="0 0 22 22"><rect x="5" y="2" width="2" height="18"/><rect x="14" y="2" width="3" height="18"/></svg>FOOD &amp; DRINK</div>
        <div class="category"><svg viewBox="0 0 22 22"><path d="M11 3l9 8h-3v8h-4v-5h-4v5H5v-8H2z"/></svg>REAL ESTATE</div>
      </div>
      <div class="feed-row">
        <div class="category"><svg viewBox="0 0 22 22"><line x1="3" y1="19" x2="19" y2="3" stroke="#111" stroke-width="3"/><line x1="3" y1="3" x2="19" y2="19" stroke="#111" stroke-width="3"/></svg>LOCAL SERVICES</div>
        <div class="category"><svg viewBox="0 0 22 22"><rect x="2" y="3" width="18" height="12" fill="none" stroke="#111" stroke-width="2"/><rect x="7" y="17" width="8" height="2"/></svg>MASS MEDIA</div>
        <div class="category"><svg viewBox="0 0 22 22"><path d="M14 3a8 8 0 1 0 5 13A7 7 0 0 1 14 3z"/></svg>NIGHTLIFE</div>
        <div class="category"><svg viewBox="0 0 22 22"><path d="M2 20V4h2v14h16v2z"/><path d="M5 17l4-6 3 3 4-7 3 4v6z"/></svg>PROFESSIONAL SERVICES</div>
      </div>
      <div class="feed-row">
        <div class="category"><svg viewBox="0 0 22 22"><circle cx="6" cy="17" r="2.5"/><circle cx="16" cy="17" r="2.5"/><circle cx="11" cy="10" r="4"/></svg>PETS</div>
        <div class="category"><svg viewBox="0 0 22 22"><path d="M2 9h18l-2 10H4z"/></svg>SHOPPING</div>
        <div class="category"><svg viewBox="0 0 22 22"><rect x="5" y="2" width="2" height="18"/><rect x="14" y="2" width="3" height="18"/></svg>RESTAURANTS</div>
        <div class="category"><svg viewBox="0 0 22 22"><path d="M11 2l9 5H2z"/><rect x="4" y="9" width="2" height="9"/><rect x="10" y="9" width="2" height="9"/><rect x="16" y="9" width="2" height="9"/><rect x="2" y="18" width="18" height="2"/></svg>PUBLIC SERVICES &amp; GOVERNMENT</div>
      </div>
    </div>
    <h2 class="tagline">SAVE YOUR TIME LIVE BETTER</h2>
    <div class="signin-row">
      <div class="social-connect"><span class="square"><span></span></span><span class="label">Connect with Friendlyn</span></div>
      <span class="default-signin">or <b>Sign In</b> by default way</span>
    </div>
  </section>

  <footer class="site-footer">
    <span>About us</span><span>|</span><span>Blog</span><span>|</span><span>Business</span><span>|</span><span>Jobs</span><span>|</span><span>Privacy</span><span>|</span><span>Faq's</span><span>|</span><span>Contact Us</span>
  </footer>
</body>
</html>
```